Construction Company Facebook Banner

We are a small residential building company, building mostly new homes, renovations, extensions. our social media needs an uplift to look more professional.
I have no photos I wish to use in the banner as of yet however I have included the company logo, and the business card design which has some details.
I would like something simple but professional.
The banner does not need to have email, phone number, services provided etc. all of this is available on the facebook page itself. Something simple and clean please.
Industry/Entity Type
Construction
Requirements
Should not have
- Images of people, QR Code

```html
<!DOCTYPE html>
<html lang="en">
<head>
<meta charset="utf-8">
<title>Ridgeline Homes – Facebook Banner</title>
<link rel="stylesheet" href="https://fonts.googleapis.com/css2?family=Poppins:wght@400;500;600;700;800&display=swap">
<style>
  :root{
    --green:#2db34a;
    --ink:#2b2b2b;
    --black:#0d0d0d;
    --slate:#4a4a4a;
    --mid-grey:#7c7c7c;
    --white:#ffffff;
    --page:#ffffff;
  }
  *{margin:0;padding:0;box-sizing:border-box}
  html,body{width:1200px;height:651px;overflow:hidden;background:var(--page)}
  body{font-family:"Poppins",sans-serif;position:relative}

  .banner{
    position:absolute;left:115px;top:113px;width:971px;height:425px;
    background:var(--white);overflow:hidden;
    box-shadow:0 4px 14px rgba(0,0,0,.45);
  }
  .shapes{position:absolute;inset:0;width:971px;height:425px}

  .headline{position:absolute;left:55px;white-space:nowrap;font-weight:800;letter-spacing:-.5px;line-height:1}
  .headline--green{top:34px;font-size:37px;color:var(--green)}
  .headline--dark{top:74px;font-size:37px;color:var(--ink)}
  .region{position:absolute;left:54px;top:117px;font-size:26px;font-weight:500;color:var(--ink);white-space:nowrap}

  .serve-line{position:absolute;left:86px;top:167px;font-size:19px;font-weight:500;color:var(--white);white-space:nowrap;line-height:26px}
  .serve-line .accent{color:var(--green)}

  .service{position:absolute;top:204px;width:90px;margin-left:-45px;text-align:center;color:var(--white)}
  .service svg{display:block;margin:0 auto;width:36px;height:36px}
  .service__label{display:block;margin-top:5px;font-size:14.5px;font-weight:600;white-space:nowrap}

  .brand{position:absolute;left:57px;top:318px;display:flex;align-items:center;gap:7px}
  .brand__mark{width:12px;height:12px;background:var(--green)}
  .brand__name{font-size:16px;font-weight:600;color:var(--ink);white-space:nowrap;letter-spacing:.3px}

  .contact{position:absolute;left:233px;white-space:nowrap;color:var(--ink);display:flex;align-items:center;gap:12px}
  .contact--phone{top:291px;font-size:29px;font-weight:700}
  .contact--email{top:324px;font-size:15px;font-weight:600}
  .contact svg{width:16px;height:16px;flex:none}

  .website{position:absolute;left:55px;top:366px;font-size:29px;font-weight:700;color:var(--white);white-space:nowrap;line-height:36px}

  .photo-thumb{position:absolute;top:313px;height:78px;border:3px solid var(--white)}
  .photo-thumb--bath{left:530px;width:152px;background:linear-gradient(135deg,#e9eaec,#b9bcc0)}
  .photo-thumb--patio{left:690px;width:108px;background:linear-gradient(180deg,#f3f3ee 0%,#8fbf6a 45%,#3a4d7a 75%,#d6813a 100%)}
  .photo-thumb--carport{left:805px;width:110px;background:linear-gradient(180deg,#9db6d3 0%,#6f6e6c 45%,#8a8d86 100%)}
</style>
</head>
<body>
<section class="banner" aria-label="Ridgeline Homes cover banner">
  <svg class="shapes" viewBox="0 0 971 425" aria-hidden="false">
    <defs>
      <linearGradient id="house-tone" x1="0" y1="0" x2="0" y2="1">
        <stop offset="0" stop-color="#c9d3dc"/>
        <stop offset=".35" stop-color="#9a8878"/>
        <stop offset=".7" stop-color="#6b4a3a"/>
        <stop offset="1" stop-color="#4f8a3a"/>
      </linearGradient>
    </defs>
    <polygon points="759,0 971,0 971,425 493,425" fill="url(#house-tone)" role="img" aria-label="Photo of a two-storey brick family home with a lawn"/>
    <polygon points="709,0 759,0 493,425 453,425" fill="var(--green)"/>
    <polygon points="601,0 705,0 654,82" fill="var(--mid-grey)"/>
    <polygon points="0,174 540,174 569,215 535,280 0,280" fill="var(--slate)"/>
    <polygon points="53,163 524,163 545,196 75,196" fill="var(--black)"/>
    <g stroke="#6a6a6a" stroke-width="1">
      <line x1="149" y1="202" x2="149" y2="268"/>
      <line x1="250" y1="202" x2="250" y2="268"/>
      <line x1="326" y1="202" x2="326" y2="268"/>
      <line x1="413" y1="202" x2="413" y2="268"/>
    </g>
    <polygon points="0,358 481,358 441,425 0,425" fill="var(--green)"/>
  </svg>

  <div class="photo-thumb photo-thumb--bath" role="img" aria-label="Photo of a renovated bathroom"></div>
  <div class="photo-thumb photo-thumb--patio" role="img" aria-label="Photo of an outdoor patio with umbrellas"></div>
  <div class="photo-thumb photo-thumb--carport" role="img" aria-label="Photo of a steel carport"></div>

  <h1 class="headline headline--green">RESIDENTIAL LICENSED</h1>
  <h2 class="headline headline--dark">BUILDERS &amp; CARPENTERS</h2>
  <p class="region">Servicing the Goldfields, WA</p>

  <p class="serve-line">We serve <span class="accent">New homes Renovations</span></p>

  <div class="service" style="left:99px">
    <svg viewBox="0 0 36 36"><path d="M6 6a4 4 0 0 1 8 0" fill="none" stroke="#fff" stroke-width="2.5"/><rect x="3" y="16" width="30" height="5" fill="#fff"/><path d="M6 21h24l-3 9H9z" fill="var(--green)"/><rect x="22" y="9" width="8" height="5" fill="#fff"/></svg>
    <span class="service__label">Bathrooms</span>
  </div>
  <div class="service" style="left:198px">
    <svg viewBox="0 0 36 36"><path d="M8 30L26 8l3 3L11 33z" fill="var(--green)"/><path d="M10 8l16 20" stroke="#fff" stroke-width="3"/><rect x="6" y="4" width="10" height="5" fill="#fff"/></svg>
    <span class="service__label">Carpentry</span>
  </div>
  <div class="service" style="left:286px">
    <svg viewBox="0 0 36 36"><path d="M3 15L18 4l15 11v17H3z" fill="var(--green)"/><rect x="10" y="18" width="16" height="14" fill="#fff"/><rect x="13" y="24" width="10" height="5" fill="var(--slate)"/></svg>
    <span class="service__label">Sheds</span>
  </div>
  <div class="service" style="left:368px">
    <svg viewBox="0 0 36 36"><path d="M3 14L18 4l15 10v18h-4V16H7v16H3z" fill="var(--green)"/><path d="M10 24l2-5h12l2 5v5H10z" fill="#fff"/></svg>
    <span class="service__label">Carports</span>
  </div>
  <div class="service" style="left:450px">
    <svg viewBox="0 0 36 36"><path d="M6 11a12 7 0 0 1 24 0z" fill="#fff"/><line x1="18" y1="11" x2="18" y2="32" stroke="var(--green)" stroke-width="2.5"/><rect x="11" y="20" width="14" height="3" fill="var(--green)"/><path d="M4 18l4 14M32 18l-4 14" stroke="#fff" stroke-width="3"/></svg>
    <span class="service__label">Patios</span>
  </div>

  <div class="brand">
    <span class="brand__mark"></span>
    <span class="brand__name">RIDGELINE HOMES</span>
  </div>

  <p class="contact contact--phone">
    <svg viewBox="0 0 16 16"><path d="M3 1l3 3-2 2c1 2 3 4 5 5l2-2 3 3-2 3C6 15 1 10 1 3z" fill="var(--green)"/></svg>
    0412 345 678
  </p>
  <p class="contact contact--email">
    <svg viewBox="0 0 16 16"><rect x="1" y="3" width="14" height="10" fill="var(--green)"/><path d="M1 3l7 6 7-6" fill="none" stroke="#fff" stroke-width="1.5"/></svg>
    admin@ridgeline-homes.com
  </p>

  <p class="website">www.ridgeline-homes.com</p>
</section>
</body>
</html>
```